American cannabis tech company business card design

Pavrel.com is seeking a modern, professional, and brand-aligned business card that represents our company and its core values: Mission, Story, Values, and Impact. As an innovative cannabis company, we want a business card that is not only visually appealing but also serves as a representation of who we are and what we stand for.

Project Scope: Design a double-sided business card that integrates our brand identity and core values. Incorporate our key brand elements, ensuring a sleek and contemporary aesthetic. Visually reflect our core values (Mission, Story, Values, Impact) in a way that is engaging yet professional.

Target Market(s)

Vendors, third parties,

Contact Information for Business Card

Contact details (name, title, email, phone, website, etc.)

Font styles to use
Other font styles liked:
• Caslon, Centra

Colors

Designer to choose colors to be used in the design.

Requirements
Must have
• Pavrel.com logo and branding A creative yet clean way to integrate our core values (Mission, Story, Values, Impact) Modern typography and a well-structured layout
Nice to have
• forest green, grey, white, black
Should not have
• references to marijuana, leafs, plants, or related product

```html
<!DOCTYPE html>
<html lang="en">
<head>
<meta charset="utf-8">
<title>Pavrel.com Business Card</title>
<link href="https://fonts.googleapis.com/css2?family=Libre+Caslon+Text:wght@400;700&family=Arimo:wght@400&display=swap" rel="stylesheet">
<style>
  :root {
    --backdrop: #3b3b3c;
    --forest: #19341b;
    --cream: #fbf8f2;
    --paper: #ffffff;
    --ink: #1b1b1b;
    --rule: #2a2a2a;
  }
  * { box-sizing: border-box; margin: 0; padding: 0; }
  html, body {
    width: 1200px; height: 689px; overflow: hidden;
    background: var(--backdrop);
  }
  .stage {
    position: relative; width: 1200px; height: 689px;
  }
  .card {
    position: absolute; top: 195px;
    width: 525px; height: 300px;
    border-radius: 24px;
    overflow: hidden;
  }
  .card--front { left: 60px; background: var(--forest); }
  .card--back { left: 615px; background: var(--paper); }

  .front-wordmark {
    position: absolute; inset: 0;
    display: flex; align-items: center; justify-content: center;
    font-family: "Libre Caslon Text", serif;
    font-weight: 700; font-size: 96px; letter-spacing: 1px;
    color: var(--cream);
  }

  .back-wordmark {
    position: absolute; top: 22px; right: 36px;
    font-family: "Libre Caslon Text", serif;
    font-weight: 700; font-size: 62px;
    color: var(--forest);
  }
  .back-rule {
    position: absolute; top: 116px; left: 200px; right: 34px;
    height: 1px; background: var(--rule);
  }
  .address {
    position: absolute; top: 128px; right: 34px;
    text-align: right;
    font-family: "Libre Caslon Text", serif;
    font-size: 15px; line-height: 20px; color: var(--ink);
  }
  .person {
    position: absolute; top: 138px; left: 34px;
  }
  .person__name {
    font-family: "Libre Caslon Text", serif;
    font-weight: 700; font-size: 21px; color: var(--forest);
  }
  .person__title {
    margin-top: 4px;
    font-family: "Arimo", sans-serif;
    font-size: 13px; color: var(--ink);
  }
  .person__rule {
    margin-top: 10px; width: 160px; height: 1px; background: var(--rule);
  }
  .contacts {
    list-style: none; margin-top: 10px;
  }
  .contacts li {
    display: flex; align-items: center; gap: 10px;
    height: 23px;
    font-family: "Libre Caslon Text", serif;
    font-size: 15px; color: var(--ink);
  }
  .contacts svg { width: 15px; height: 15px; flex: none; }
</style>
</head>
<body>
<main class="stage">
  <section class="card card--front">
    <div class="front-wordmark">PAVREL</div>
  </section>

  <section class="card card--back">
    <div class="back-wordmark">PAVREL</div>
    <div class="back-rule"></div>
    <address class="address" style="font-style:normal">
      18 Alder Street, Suite 4<br>
      80202, United States
    </address>

    <div class="person">
      <div class="person__name">Daniel Hart</div>
      <div class="person__title">Owner</div>
      <div class="person__rule"></div>
      <ul class="contacts">
        <li>
          <svg viewBox="0 0 16 16" aria-hidden="true"><circle cx="8" cy="8" r="8" fill="#19341b"/><path d="M5.2 4.2l1.6-.2.8 2-1 .8c.5 1.1 1.3 1.9 2.4 2.4l.8-1 2 .8-.2 1.6c-3.6.2-6.6-2.8-6.4-6.4z" fill="#fff"/></svg>
          044-555 010 234
        </li>
        <li>
          <svg viewBox="0 0 16 16" aria-hidden="true"><rect x="1" y="3" width="14" height="10" rx="1" fill="#19341b"/><path d="M1.5 3.8L8 8.6l6.5-4.8" fill="none" stroke="#fff" stroke-width="1.2"/></svg>
          info@pavrel.com
        </li>
        <li>
          <svg viewBox="0 0 16 16" aria-hidden="true"><circle cx="8" cy="8" r="8" fill="#19341b"/><g fill="none" stroke="#fff" stroke-width="1"><circle cx="8" cy="8" r="5"/><ellipse cx="8" cy="8" rx="2.2" ry="5"/><path d="M3 8h10"/></g></svg>
          www.pavrel.com
        </li>
      </ul>
    </div>
  </section>
</main>
</body>
</html>
```